Brightmoor - a website to encourage people to spend time in nature

I have a squarespace site with some content on it but the squarespace template doesn't completely suit my needs, I keep fiddling with the template but actually I need some professional help to get it looking the way I want and with the right 'mood'.
The website is for "Brightmoor" - it will be a blog where I write about the importance of nature for good health. I also want to use the website to market services such as outdoor coaching, retreats and walking workshops.
This has been in my head for a LONG time and I currently only use instagram for micro-blogs but it's time for me to get this moving. I've previously engaged other designers on branding for it but they just didn't get it quite the way that I wanted it and I wasn't completely happy with the results. It's been a process for me as to what I want but in the meantime I just didn't come back to the design aspect of it now. I'm looking for a designer who understands the purpose of the website, the ethos and can help me realise this into a design that's clean, clear and simple.

Please note that I have a domain (brightmoor.org) and a lot of content drafted on squarespace already. I have published it with password protection - password is brightmoor2020 - it still has some of the original template on it, but does have some content. Don't take it as anything to follow in particular, i am looking for fresh eyes and fresh ideas.

Target Market(s)

There are three main groups that I want to target - people who are suffering from stress and anxiety, people who treat them and parents who want to get their kids outside (thereby preventing stress and anxiety)

Contact Information for Business Card

Joan Petrie
Brightmoor
Telephone +44 7700 900417
brightmoor@mailvane.com

Logo Text

Brightmoor - if that. I have an idea that the logo should have a leaf on it somewhere, or maybe just be a leaf.

Coding

Coded - Design and coding required

Number of Pages Required

5+ page

Font styles to use
Serif
Sans Serif

Colors
add136
33b8a4
34a6d7
3377b5

Requirements
Must have
• Space for lots of images. The ability for me to edit the pages if I need to. Be user friendly. Look beautiful.
• For an idea of the images I use and the content I'm interested in writing about have a look at @brightmoor on instagram.
• That pop up about cookies so I am complying with data laws.
Should not have
• Must not be too 'busy' I'd like to avoid too much movement.

```html
<!DOCTYPE html>
<html lang="en">
<head>
<meta charset="utf-8">
<title>Brightmoor</title>
<link href="https://fonts.googleapis.com/css2?family=Poppins:ital,wght@0,400;0,500;0,600;0,700;1,400;1,600&family=Roboto:wght@400;500;700&display=swap" rel="stylesheet">
<style>
:root{
  --sky:#34a6d7;
  --teal:#33b8a4;
  --lime:#add136;
  --link:#3377b5;
  --accept:#1ecf8a;
  --decline:#e10a27;
  --ink:#111;
  --body:#666;
  --white:#fff;
  --footer:#000;
}
*{box-sizing:border-box;margin:0;padding:0}
html,body{width:1200px;height:3899px;overflow:hidden}
body{position:relative;font-family:'Roboto',sans-serif;color:var(--body);background:var(--white)}
.abs{position:absolute}
.center{left:0;width:1200px;text-align:center}

/* cookie bar */
.cookie-bar{top:0;left:0;width:1200px;height:132px;background:var(--sky);color:var(--white)}
.cookie-title{top:17px;font:500 18px 'Roboto',sans-serif}
.cookie-text{top:42px;font:400 14.5px 'Roboto',sans-serif}
.cookie-btn{top:74px;height:36px;border-radius:18px;font:700 12px 'Roboto',sans-serif;color:var(--white);line-height:36px;text-align:center}
.cookie-accept{left:416px;width:170px;background:var(--accept)}
.cookie-decline{left:596px;width:170px;background:var(--decline)}
.cookie-close{left:1143px;top:12px;width:44px;height:44px;border-radius:50%;background:#e9eef1}

/* hero */
.hero{top:132px;left:0;width:1200px;height:649px;
  background:linear-gradient(90deg,#4b4a48 0%,#6e6863 35%,#7d5c52 70%,#8a4e44 100%)}
.hero-sky{top:132px;left:0;width:1200px;height:320px;background:linear-gradient(180deg,#b7bcb8 0%,rgba(160,160,158,.6) 60%,rgba(0,0,0,0) 100%)}
.header{top:132px;left:0;width:1200px;height:134px;background:rgba(210,214,210,.35)}
.logo{left:118px;top:180px;font:700 34px 'Poppins',sans-serif;color:var(--white);display:flex;align-items:center;gap:10px}
.logo-dot{width:14px;height:14px;border-radius:50%;background:var(--lime)}
.nav{top:201px;left:441px;display:flex;gap:36px;font:500 14px 'Roboto',sans-serif;color:var(--white)}
.nav .active{position:relative}
.nav .active::after{content:"";position:absolute;left:0;right:0;top:30px;height:3px;background:var(--white)}
.social{width:48px;height:48px;border:2px solid var(--white);border-radius:50%}
.hero-title{top:440px;font:700 52px 'Poppins',sans-serif;color:var(--white)}
.hero-text{top:514px;font:500 17.5px/28px 'Roboto',sans-serif;color:var(--white)}

/* section headings */
.section-title{font:700 39px 'Poppins',sans-serif;color:var(--ink)}
.rule{width:76px;height:4px;background:var(--teal);left:562px}

.about-text{top:940px;left:160px;width:880px;text-align:center;font:400 14.5px/26px 'Roboto',sans-serif;color:#666}

/* mission band */
.band{top:1120px;left:0;width:1200px;height:379px;background:linear-gradient(180deg,#5f6463 0%,#3d4438 50%,#2c3125 100%)}
.band-text{top:1210px;left:170px;width:860px;text-align:center;font:400 23px/34px 'Poppins',sans-serif;color:var(--white)}
.band-btn{top:1337px;left:514px;width:172px;height:61px;border:2px solid var(--white);border-radius:31px;color:var(--white);font:500 14px/57px 'Roboto',sans-serif;text-align:center}

/* service cards */
.card-img{top:1676px;width:312px;height:206px}
.card-title{top:1902px;font:700 18px 'Roboto',sans-serif;color:var(--ink)}
.card-text{top:1938px;width:260px;font:400 13.5px/26px 'Roboto',sans-serif;color:#666}
.read-more{top:2027px;font:700 13.5px 'Roboto',sans-serif;color:var(--sky);text-decoration:underline}

/* testimonial */
.quote-band{top:2132px;left:0;width:1200px;height:380px;background:linear-gradient(180deg,#2f8a78 0%,#2a8c7c 50%,#3a9a7c 100%)}
.quote-text{top:2260px;left:190px;width:820px;text-align:center;font:italic 400 20px/35px 'Poppins',sans-serif;color:#e6f2ee}
.quote-author{top:2370px;font:italic 600 19px 'Poppins',sans-serif;color:var(--white)}

/* blog */
.blog-card{top:2678px;width:312px;height:353px;background:var(--white);box-shadow:0 2px 10px rgba(0,0,0,.12);padding:24px 28px}
.blog-title{font:500 19px/26px 'Roboto',sans-serif;color:var(--ink)}
.blog-meta{margin-top:14px;display:flex;gap:24px;font:700 13.5px 'Roboto',sans-serif;color:var(--ink);align-items:center}
.blog-meta span{display:flex;align-items:center;gap:5px}
.blog-text{margin-top:14px;font:400 13.5px/25.7px 'Roboto',sans-serif;color:#777;text-align:justify}
.gallery{top:3118px;height:293px}

/* footer */
.footer{top:3504px;left:0;width:1200px;height:395px;background:var(--footer);color:var(--white)}
.foot-head{top:3580px;font:500 18px 'Roboto',sans-serif;color:var(--white)}
.foot-rule{top:3616px;width:26px;height:3px;background:var(--teal)}
.foot-list{top:3636px;list-style:none;font:400 14px/34px 'Roboto',sans-serif;color:var(--white)}
.foot-list li::before{content:"›";display:inline-block;width:26px;font-size:16px}
.contact-row{font:400 14px/26px 'Roboto',sans-serif;color:var(--white);display:flex;gap:12px}
.foot-logo{left:906px;top:3602px;font:700 30px 'Poppins',sans-serif;color:var(--white);display:flex;align-items:center;gap:8px}
.foot-divider{top:3826px;left:110px;width:980px;height:1px;background:#444}
.copyright{top:3848px;font:400 13px 'Roboto',sans-serif;color:var(--white)}
</style>
</head>
<body>

<!-- cookie notice -->
<div class="abs cookie-bar"></div>
<div class="abs center cookie-title">HEARTHLEAF COOKIES</div>
<div class="abs center cookie-text">Lorem ipsum dolor sit amet, consectetur adipiscing elit, sed do eiusmod tempor incididunt ut labore et dolore magna</div>
<div class="abs cookie-btn cookie-accept">Ok, I Accept Cookies</div>
<div class="abs cookie-btn cookie-decline">No, I Deagree</div>
<div class="abs cookie-close">
  <svg width="44" height="44" viewBox="0 0 44 44"><path d="M16 16 L28 28 M28 16 L16 28" stroke="var(--sky)" stroke-width="4" stroke-linecap="round"/></svg>
</div>

<!-- hero -->
<div class="abs hero" role="img" aria-label="Walker standing on a rocky mountain slope beside a stone wall under a misty sky"></div>
<div class="abs hero-sky"></div>
<div class="abs header"></div>
<div class="abs logo"><span class="logo-dot"></span>Brightmoor</div>
<nav class="abs nav">
  <span class="active">HOME</span><span>ABOUT US</span><span>SERVICES</span><span>BLOG</span><span>TESTIMONIALS</span>
</nav>
<div class="abs social" style="left:941px;top:186px" aria-label="Social link"></div>
<div class="abs social" style="left:997px;top:186px" aria-label="Social link"></div>
<div class="abs social" style="left:1053px;top:186px" aria-label="Social link"></div>
<h1 class="abs center hero-title">BRIGHTMOOR</h1>
<p class="abs center hero-text">Lorem ipsum dolor sit amet, consectetur adipiscing elit, sed do eiusmod tempor<br>incididunt ut labore et dolore magna aliqua. Ut enim ad</p>

<!-- about -->
<h2 class="abs center section-title" style="top:855px">ABOUT US</h2>
<div class="abs rule" style="top:918px"></div>
<p class="abs about-text">Lorem ipsum dolor sit amet, consectetur adipiscing elit, sed do eiusmod tempor incididunt ut labore et dolore magna aliqua. Ut enim ad minim veniam, quis nostrud exercitation ullamco laboris nisi ut aliquip ex ea commodo consequat. Duis aute irure dolor in reprehenderit in voluptate velit esse cillum dolore eu fugiat nulla pariatur. Excepteur sint occaecat cupidatat non proident, sunt in culpa qui officia de serunt mollit anim id est laborum.</p>

<!-- mission band -->
<div class="abs band" role="img" aria-label="Misty forested valley below low clouds"></div>
<p class="abs band-text">There are three main groups that I want to target - people who are suffering from stress and anxiety, people who treat them and parents who want to get their kids outside</p>
<div class="abs band-btn">CONTACT US</div>

<!-- services -->
<h2 class="abs center section-title" style="top:1573px">OUR SERVICES</h2>
<div class="abs rule" style="top:1637px"></div>

<div class="abs card-img" style="left:112px;background:linear-gradient(135deg,#6f6a62,#b89a82 50%,#7a7670)" role="img" aria-label="Two smiling friends outdoors"></div>
<div class="abs card-title" style="left:131px">COACHING</div>
<p class="abs card-text" style="left:131px">Only one thing better than coaching and that's coaching in the great outdoors. We believe that being out in nature</p>
<div class="abs read-more" style="left:131px">Read more »</div>

<div class="abs card-img" style="left:443px;background:linear-gradient(180deg,#6d7466,#4a4d44 60%,#5c5a54)" role="img" aria-label="Family walking together along a woodland path"></div>
<div class="abs card-title" style="left:462px">WALKING</div>
<p class="abs card-text" style="left:462px">Two sides of the same coin as far as we're concerned. The main driver is getting a message out that time in</p>
<div class="abs read-more" style="left:462px">Read more »</div>

<div class="abs card-img" style="left:773px;background:linear-gradient(180deg,#8b95a0 0%,#6b7a54 35%,#8a8a7c 60%,#7c7f3a 100%)" role="img" aria-label="Child in a red coat on a gravel trail through gorse"></div>
<div class="abs card-title" style="left:793px">RETREAT</div>
<p class="abs card-text" style="left:793px">Sometimes you just need to get away from it all. And that's where Brightmoor retreats come in. Our retreats</p>
<div class="abs read-more" style="left:793px">Read more »</div>

<!-- testimonial -->
<div class="abs quote-band" role="img" aria-label="Grassy path with a dog, tinted green"></div>
<p class="abs quote-text">Lorem ipsum dolor sit amet, consectetur adipiscing elit, sed do eiusmod tempor incididunt ut labore et dolore magna aliqua. Ut enim ad minim veniam, quis nostrud exercitation ullamco laboris nisi ut aliquip ex ea commodo consequat.</p>
<div class="abs center quote-author">- John Doe</div>

<!-- blog -->
<h2 class="abs center section-title" style="top:2584px">LATEST BLOG</h2>
<div class="abs rule" style="top:2649px"></div>

<article class="abs blog-card" style="left:112px">
  <h3 class="blog-title">Lorem ipsum dolor sit amet, consec tetur adipiscing</h3>
  <div class="blog-meta">
    <span><svg width="14" height="14" viewBox="0 0 14 14"><rect x="1" y="2" width="12" height="11" fill="none" stroke="var(--teal)" stroke-width="1.5"/><path d="M1 5h12" stroke="var(--teal)" stroke-width="1.5"/></svg>Jan 15, 2020</span>
    <span><svg width="16" height="14" viewBox="0 0 16 14"><ellipse cx="8" cy="6" rx="7" ry="5" fill="none" stroke="var(--teal)" stroke-width="1.5"/></svg>20</span>
  </div>
  <p class="blog-text">Lorem ipsum dolor sit amet, conse ctetur adipiscing elit, sed do eiusmod tempor incididunt ut labore et dolore magna aliqua. Ut enim ad minim veniam, quis nostrud exercitation ullamco laboris nisi ut aliquip ex ea commodo consequat. Duis aute irure dolor in reprehen laboris nisi</p>
</article>
<article class="abs blog-card" style="left:443px">
  <h3 class="blog-title">Lorem ipsum dolor sit amet, consec tetur adipiscing</h3>
  <div class="blog-meta">
    <span><svg width="14" height="14" viewBox="0 0 14 14"><rect x="1" y="2" width="12" height="11" fill="none" stroke="var(--teal)" stroke-width="1.5"/><path d="M1 5h12" stroke="var(--teal)" stroke-width="1.5"/></svg>Jan 15, 2020</span>
    <span><svg width="16" height="14" viewBox="0 0 16 14"><ellipse cx="8" cy="6" rx="7" ry="5" fill="none" stroke="var(--teal)" stroke-width="1.5"/></svg>20</span>
  </div>
  <p class="blog-text">Lorem ipsum dolor sit amet, conse ctetur adipiscing elit, sed do eiusmod tempor incididunt ut labore et dolore magna aliqua. Ut enim ad minim veniam, quis nostrud exercitation ullamco laboris nisi ut aliquip ex ea commodo consequat. Duis aute irure dolor in reprehen laboris nisi</p>
</article>
<article class="abs blog-card" style="left:773px">
  <h3 class="blog-title">Lorem ipsum dolor sit amet, consec tetur adipiscing</h3>
  <div class="blog-meta">
    <span><svg width="14" height="14" viewBox="0 0 14 14"><rect x="1" y="2" width="12" height="11" fill="none" stroke="var(--teal)" stroke-width="1.5"/><path d="M1 5h12" stroke="var(--teal)" stroke-width="1.5"/></svg>Jan 15, 2020</span>
    <span><svg width="16" height="14" viewBox="0 0 16 14"><ellipse cx="8" cy="6" rx="7" ry="5" fill="none" stroke="var(--teal)" stroke-width="1.5"/></svg>20</span>
  </div>
  <p class="blog-text">Lorem ipsum dolor sit amet, conse ctetur adipiscing elit, sed do eiusmod tempor incididunt ut labore et dolore magna aliqua. Ut enim ad minim veniam, quis nostrud exercitation ullamco laboris nisi ut aliquip ex ea commodo consequat. Duis aute irure dolor in reprehen laboris nisi</p>
</article>

<div class="abs gallery" style="left:112px;width:478px;background:linear-gradient(135deg,#4e5a4a,#c29a84 45%,#7e8a86)" role="img" aria-label="Two friends taking a selfie by the sea"></div>
<div class="abs gallery" style="left:608px;width:480px;background:linear-gradient(180deg,#9aa3ad 0%,#6d7a56 30%,#8c8b80 60%,#7f8038 100%)" role="img" aria-label="Child in a red coat walking a gravel trail among gorse"></div>

<!-- footer -->
<footer class="abs footer"></footer>
<div class="abs foot-head" style="left:110px">QUICK LINKS</div>
<div class="abs foot-rule" style="left:110px"></div>
<ul class="abs foot-list" style="left:110px"><li>Home</li><li>About us</li><li>Services</li><li>Blog</li><li>Testimonials</li></ul>

<div class="abs foot-head" style="left:346px">SUPPORT</div>
<div class="abs foot-rule" style="left:346px"></div>
<ul class="abs foot-list" style="left:346px"><li>Privacy policy</li><li>Terms conditions</li><li>Support</li><li>Laboris nisi</li><li>Ncididunt ut</li></ul>

<div class="abs foot-head" style="left:582px">CONTACT US</div>
<div class="abs foot-rule" style="left:582px"></div>
<div class="abs contact-row" style="left:584px;top:3637px">
  <svg width="12" height="16" viewBox="0 0 12 16"><path d="M6 15C6 15 1 9 1 5.5a5 5 0 0 1 10 0C11 9 6 15 6 15z" fill="var(--teal)"/><circle cx="6" cy="5.5" r="2" fill="#000"/></svg>
  <span>123,Lorem ipsum dolor sit amet,<br>consectetur adipiscing elit,</span>
</div>
<div class="abs contact-row" style="left:584px;top:3716px">
  <svg width="14" height="14" viewBox="0 0 14 14" style="margin-top:4px"><path d="M3 1l3 3-2 2a8 8 0 0 0 4 4l2-2 3 3-2 2C6 13 1 8 1 3z" fill="var(--teal)"/></svg>
  <span>+1 888 888 8888</span>
</div>
<div class="abs contact-row" style="left:582px;top:3776px">
  <svg width="16" height="12" viewBox="0 0 16 12" style="margin-top:7px"><rect width="16" height="12" rx="1" fill="var(--teal)"/><path d="M1 1l7 6 7-6" stroke="#000" stroke-width="1.3" fill="none"/></svg>
  <span>info@brightmoor.org</span>
</div>

<div class="abs foot-logo"><span class="logo-dot"></span>Brightmoor</div>
<div class="abs social" style="left:917px;top:3666px" aria-label="Social link"></div>
<div class="abs social" style="left:973px;top:3666px" aria-label="Social link"></div>
<div class="abs social" style="left:1029px;top:3666px" aria-label="Social link"></div>

<div class="abs foot-divider"></div>
<div class="abs center copyright">© Copyrights 2020. Brightmoor | All rights Reserved</div>

</body>
</html>
```